Homepage for the brisk-find Web Application

At the end of this text, you will find a link to a website that is under construction for a webApp that I intend to launch soon. The contest goal is for you to make redesign the homepage in a nice, fresh, modern Style. Only design, no coding necessary. It needs to have a responsive version for small screens like smart phones. Attached is the text for it, and some images that you may use. You are welcome to find or create additional supporting images. You can use PixTrove.example or similar service to find new images as long as I can purchase the non-exclusive use rights for the images at similar prices. The contest is just for the home page. However, the winner, if I like the work and we can agree on a fair price, could be contracted on a one-on-one basis to do the rest of the site. You are welcome to suggest minor changes like font sizes and minor variations on the Header banner, but that banner is consistent with the user interface of the application therefore should not change too much. The information should flow somewhat continually without much use of side bars or things like that.
https://www.brisk-find.example
Sincerely,
Marco D. Ferral

```html
<!DOCTYPE html>
<html lang="en">
<head>
<meta charset="utf-8">
<title>Brisk-Find — Find any document or item instantly</title>
<link href="https://fonts.googleapis.com/css2?family=Lato:wght@400;700;900&display=swap" rel="stylesheet">
<style>
:root{
  --teal:#3fb3aa;
  --teal-dark:#2a9d95;
  --orange:#ea5234;
  --ink:#1f1f1f;
  --text:#2b2b2b;
  --hero-top:#bff6f8;
  --hero-bottom:#a9eef1;
  --grey-band:#efefef;
  --footer:#2a2a2a;
  --footer-bottom:#1e1e1e;
  --footer-text:#cfcfcf;
  --white:#ffffff;
}
*{box-sizing:border-box;margin:0;padding:0}
html,body{width:1200px;height:3745px;overflow:hidden}
body{position:relative;font-family:'Lato',sans-serif;color:var(--text);background:var(--white)}
.abs{position:absolute}
.hero{left:0;top:0;width:1200px;height:746px;background:linear-gradient(180deg,var(--hero-top),var(--hero-bottom))}
.brand{left:74px;top:34px;display:flex;align-items:center;gap:10px;font-size:38px;font-weight:400;color:var(--orange)}
.brand-dot{width:34px;height:34px;border-radius:50%;border:3px solid var(--ink);background:transparent}
.pill{display:flex;align-items:center;justify-content:center;border-radius:30px;font-weight:700;color:var(--white);font-size:15px;letter-spacing:.3px}
.btn-trial{left:874px;top:31px;width:118px;height:45px;background:var(--teal)}
.btn-login{left:1009px;top:31px;width:117px;height:45px;background:var(--orange)}
.nav{top:103px;font-size:15px;font-weight:900;color:var(--ink)}
.hero-title{left:74px;top:288px;font-size:55px;line-height:58px;font-weight:900;color:var(--orange)}
.hero-text{left:74px;top:420px;width:540px;font-size:17px;line-height:33px;color:var(--ink)}
.btn-solid{background:var(--teal);color:var(--white);font-size:18px}
.btn-outline{border:2px solid var(--orange);color:var(--orange);background:var(--white);font-size:18px;border-radius:30px;display:flex;align-items:center;justify-content:center;font-weight:700}
.art{border-radius:24px}
.band{left:74px;top:713px;width:1052px;height:71px;border-radius:36px;background:var(--orange);color:var(--white);font-size:22px;font-weight:900;display:flex;align-items:center;justify-content:center}
.section-title{left:0;width:1200px;text-align:center;font-weight:700;color:var(--ink)}
.accent{color:var(--teal)}
.sub-title{font-size:37px;line-height:43px;font-weight:700;color:var(--teal)}
.body-copy{font-size:16px;line-height:32px;color:var(--ink)}
.item-title{font-size:21px;line-height:29px;font-weight:700;color:var(--orange)}
.item-copy{font-size:16px;line-height:27.8px;color:var(--ink)}
.icon{width:44px;height:44px}
.checklist{left:74px;top:2404px;width:520px;list-style:none}
.checklist li{position:relative;padding-left:34px;font-size:16px;line-height:28px;color:var(--ink);margin-bottom:4px}
.checklist svg{position:absolute;left:0;top:6px}
.reviews{left:0;top:2858px;width:1200px;height:519px;background:var(--grey-band)}
.quote{left:0;width:1200px;top:2988px;text-align:center}
.review-text{left:172px;top:3060px;width:856px;text-align:center;font-size:14px;line-height:27px;color:var(--ink)}
.avatar{width:100px;height:100px;border-radius:50%;background:radial-gradient(circle at 40% 35%,#7fb7d8,#3f6f96)}
.person{width:160px;text-align:center}
.person-name{font-size:16px;font-weight:700;color:var(--orange);margin-top:16px}
.person-loc{font-size:13px;color:#555;margin-top:2px}
.footer{left:0;top:3377px;width:1200px;height:318px;background:var(--footer)}
.footer-bottom{left:0;top:3695px;width:1200px;height:50px;background:var(--footer-bottom)}
.foot-head{font-size:20px;font-weight:700;color:var(--teal);top:3423px}
.foot-link{font-size:14px;color:var(--footer-text)}
.foot-link b{color:var(--white);margin-right:14px;font-weight:900}
.input{left:884px;top:3468px;width:242px;height:48px;border-radius:24px;background:var(--white);font-size:14px;color:#333;display:flex;align-items:center;padding-left:18px}
.social{width:22px;height:22px;border-radius:50%;background:#bdbdbd;top:3712px}
</style>
</head>
<body>

<!-- Hero -->
<div class="abs hero"></div>
<div class="abs brand"><span class="brand-dot"></span>Brisk-Find</div>
<div class="abs pill btn-trial">FREE-TRIAL</div>
<div class="abs pill btn-login">LOG IN</div>
<nav>
  <span class="abs nav" style="left:486px">ABOUT</span>
  <span class="abs nav" style="left:575px">PRICING</span>
  <span class="abs nav" style="left:672px">BLOG</span>
  <span class="abs nav" style="left:748px">FAQS</span>
  <span class="abs nav" style="left:822px">SUPPORT</span>
  <span class="abs nav" style="left:928px">REVIEWS</span>
  <span class="abs nav" style="left:1031px">CONTACT US</span>
</nav>
<h1 class="abs hero-title">Find any document<br>or item instantly!</h1>
<p class="abs hero-text">Brisk-Find is a system that allows you to quickly search for the location of every item that you store or file.</p>
<div class="abs pill btn-solid" style="left:74px;top:515px;width:179px;height:60px">Learn More</div>
<div class="abs art" role="img" aria-label="Illustration of a businessman pulling an item from a drawer in a large smartphone" style="left:669px;top:175px;width:378px;height:538px;background:linear-gradient(160deg,#7fdad6,#2fa7a5)"></div>
<div class="abs band">Keeping track of all your paper documents and other belongings has never been easier!</div>

<!-- Why use -->
<h2 class="abs section-title" style="top:830px;font-size:42px;line-height:54px">Why use a storage management system<br>like <span class="accent">Brisk-Find?</span></h2>
<div class="abs art" role="img" aria-label="Illustration of a man filing folders in drawers rising out of a laptop" style="left:109px;top:996px;width:451px;height:459px;background:linear-gradient(160deg,#9ae7e5,#2aa0a3)"></div>
<h3 class="abs sub-title" style="left:615px;top:1013px">Managing paper<br>documents</h3>
<p class="abs body-copy" style="left:615px;top:1114px;width:514px">Most people and businesses have a variety of documents that need to be filed.The problem is how to do it efficiently so that anything you need can easily be found, even well into the future. Normally, you'd put them in folders on file drawers, sorted in some sort of fashion. But which standard is correct for all kinds of documents? There is no set criterion for every kind of document, so you need to use a combination of them.</p>
<div class="abs btn-outline" style="left:615px;top:1375px;width:178px;height:55px">Learn More</div>

<!-- Non-document objects -->
<h2 class="abs section-title sub-title" style="top:1521px;color:var(--teal)">Managing any non-document objects</h2>
<p class="abs" style="left:0;width:1200px;top:1594px;text-align:center;font-size:16px;color:var(--ink)">The same is true of storing any other kind of objects. Common examples include:</p>

<svg class="abs icon" style="left:72px;top:1664px" viewBox="0 0 44 44" fill="none" stroke="var(--teal)" stroke-width="2"><path d="M6 16 L22 10 L38 16 L22 22 Z"/><path d="M6 16 V32 L22 38 L38 32 V16"/><path d="M22 22 V38"/><path d="M6 16 L2 10 L18 5 L22 10"/><path d="M38 16 L42 10 L26 5 L22 10"/></svg>
<div class="abs item-title" style="left:150px;top:1660px">Storage boxes, closets, warehouses,<br>and shelves</div>
<p class="abs item-copy" style="left:150px;top:1727px;width:432px">Anything that you put away in storage, would better be indexed with a system that lets you find what you're looking for instantly. Otherwise, you are better off getting rid of those items. In addition to helping you find any object quickly and easily, proper use of Brisk-Find could help you save lots of space!</p>

<svg class="abs icon" style="left:80px;top:1922px" viewBox="0 0 44 44" fill="none" stroke="var(--teal)" stroke-width="2"><path d="M8 4 H14 V12 L18 18 V42 H4 V18 L8 12 Z"/><path d="M4 26 H18 V36 H4"/><path d="M26 20 H38 Q38 32 32 32 Q26 32 26 20 Z"/><path d="M32 32 V42 M27 42 H37"/></svg>
<div class="abs item-title" style="left:150px;top:1919px">Wines</div>
<p class="abs item-copy" style="left:150px;top:1957px;width:432px">Maintaining a constant temperature is essential for good care of quality wines. If you are a wine enthusiast, and have even a small wine cellar fridge, keeping your wines indexed on our system would prove invaluable in selecting and locating a wine bottle for any moment without opening that cellar fridge door for too long.</p>

<svg class="abs icon" style="left:620px;top:1664px" viewBox="0 0 44 44" fill="none" stroke="var(--teal)" stroke-width="2"><rect x="6" y="3" width="32" height="38" rx="4"/><path d="M6 30 H38"/><rect x="14" y="9" width="16" height="4"/><rect x="14" y="16" width="16" height="4"/></svg>
<div class="abs item-title" style="left:691px;top:1660px">Books</div>
<p class="abs item-copy" style="left:691px;top:1698px;width:436px">Whether you keep your books on display on shelves, or stored in boxes, you shouldkeep them indexed if you ever want to find any of them in the future.</p>

<svg class="abs icon" style="left:618px;top:1810px" viewBox="0 0 44 44" fill="none" stroke="var(--teal)" stroke-width="2"><rect x="2" y="4" width="40" height="8"/><rect x="5" y="12" width="34" height="28"/><rect x="16" y="20" width="12" height="6"/></svg>
<div class="abs item-title" style="left:691px;top:1806px">Safety boxes</div>
<p class="abs item-copy" style="left:691px;top:1844px;width:436px">It is common for people to forget exactly which valuables they have stored in their safety boxes or bank safety deposit boxes.</p>

<svg class="abs icon" style="left:620px;top:1955px" viewBox="0 0 44 44" fill="none" stroke="var(--teal)" stroke-width="2"><rect x="3" y="6" width="26" height="20" rx="2"/><path d="M3 22 H29"/><path d="M10 32 H22 M16 26 V32"/><rect x="24" y="18" width="14" height="22" rx="2"/><circle cx="31" cy="36" r="1"/><path d="M14 10 L20 14 L14 18"/></svg>
<div class="abs item-title" style="left:691px;top:1951px">Moving boxes</div>
<p class="abs item-copy" style="left:691px;top:1989px;width:442px">It is always a good idea to record in detail the contents of each box when you move. Since Brisk-Find works well on any modern smartphone, it is easy to record each item as you pack it. After the move, the system makes it easy for you to check that everything that you packed arrived as it should.</p>

<div class="abs btn-outline" style="left:512px;top:2188px;width:177px;height:55px">Learn More</div>

<!-- Why Brisk-Find -->
<h2 class="abs sub-title" style="left:74px;top:2336px;font-size:40px">Why Brisk-Find?</h2>
<ul class="abs checklist">
  <li><svg width="18" height="18" viewBox="0 0 18 18"><circle cx="9" cy="9" r="9" fill="var(--teal)"/><path d="M5 9.5 L8 12 L13 6.5" stroke="#fff" stroke-width="2" fill="none"/></svg>It is extremely easy to use.</li>
  <li><svg width="18" height="18" viewBox="0 0 18 18"><circle cx="9" cy="9" r="9" fill="var(--teal)"/><path d="M5 9.5 L8 12 L13 6.5" stroke="#fff" stroke-width="2" fill="none"/></svg>It Adapts to your stile.Since each catalog can have 1 or more levels of depth (folders and sub-folders), Brisk-Find does not force you to use a specific filing or storage methodology.</li>
  <li><svg width="18" height="18" viewBox="0 0 18 18"><circle cx="9" cy="9" r="9" fill="var(--teal)"/><path d="M5 9.5 L8 12 L13 6.5" stroke="#fff" stroke-width="2" fill="none"/></svg>It's very affordable. Checkout our pricing plans!</li>
  <li><svg width="18" height="18" viewBox="0 0 18 18"><circle cx="9" cy="9" r="9" fill="var(--teal)"/><path d="M5 9.5 L8 12 L13 6.5" stroke="#fff" stroke-width="2" fill="none"/></svg>Since it is online, your data is available almost anywhere<br>in the world.</li>
  <li><svg width="18" height="18" viewBox="0 0 18 18"><circle cx="9" cy="9" r="9" fill="var(--teal)"/><path d="M5 9.5 L8 12 L13 6.5" stroke="#fff" stroke-width="2" fill="none"/></svg>Data encryption ensures that your information is always<br>private, safe, and secure.</li>
</ul>
<div class="abs btn-outline" style="left:76px;top:2699px;width:225px;height:55px">30 Day Free Trial</div>
<div class="abs art" role="img" aria-label="Illustration of a businessman with a large bottle beside drawers in a smartphone" style="left:710px;top:2317px;width:301px;height:454px;background:linear-gradient(160deg,#a7ece9,#35aaa8)"></div>

<!-- Reviews -->
<div class="abs reviews"></div>
<h2 class="abs section-title" style="top:2904px;font-size:42px">Customer Reviews</h2>
<svg class="abs" style="left:573px;top:2988px" width="54" height="46" viewBox="0 0 54 46"><path d="M2 2 H24 V22 Q24 40 8 46 L6 40 Q14 34 14 26 H2 Z M30 2 H52 V22 Q52 40 36 46 L34 40 Q42 34 42 26 H30 Z" fill="var(--orange)"/></svg>
<p class="abs review-text">Sed ut perspiciatis unde omnis iste natus error sit voluptatem accusantium doloremque laudantium, totam rem aperiam, eaque ipsa quae ab illo inventore veritatis et quasi architecto beatae vitae dicta sunt explicabo. Nemo enim ipsam voluptatem quia voluptas sit aspernatur aut odit aut fugit, sed quia consequuntur magni dolores eos qui ratione voluptatem sequi nesciunt.</p>
<svg class="abs" style="left:74px;top:3110px" width="20" height="34" viewBox="0 0 20 34"><path d="M17 3 L4 17 L17 31" stroke="#333" stroke-width="4" fill="none"/></svg>
<svg class="abs" style="left:1106px;top:3110px" width="20" height="34" viewBox="0 0 20 34"><path d="M3 3 L16 17 L3 31" stroke="#333" stroke-width="4" fill="none"/></svg>
<div class="abs person" style="left:364px;top:3162px"><div class="avatar" role="img" aria-label="Customer portrait" style="margin:0 auto"></div><div class="person-name">Name Heading</div><div class="person-loc">Location</div></div>
<div class="abs person" style="left:518px;top:3162px"><div class="avatar" role="img" aria-label="Customer portrait" style="margin:0 auto;background:radial-gradient(circle at 40% 35%,#c9a27e,#5a3f2c)"></div><div class="person-name">Name Heading</div><div class="person-loc">Location</div></div>
<div class="abs person" style="left:673px;top:3162px"><div class="avatar" role="img" aria-label="Customer portrait" style="margin:0 auto"></div><div class="person-name">Name Heading</div><div class="person-loc">Location</div></div>

<!-- Footer -->
<footer>
<div class="abs footer"></div>
<div class="abs foot-head" style="left:74px">Quick Links</div>
<div class="abs foot-link" style="left:74px;top:3469px"><b>»</b>About</div>
<div class="abs foot-link" style="left:74px;top:3510px"><b>»</b>Pricing</div>
<div class="abs foot-link" style="left:74px;top:3550px"><b>»</b>Blog</div>
<div class="abs foot-link" style="left:74px;top:3591px"><b>»</b>FAQs</div>
<div class="abs foot-link" style="left:207px;top:3469px"><b>»</b>Support</div>
<div class="abs foot-link" style="left:207px;top:3510px"><b>»</b>Reviews</div>
<div class="abs foot-link" style="left:207px;top:3550px"><b>»</b>Contact Us</div>

<div class="abs foot-head" style="left:352px">Support</div>
<div class="abs foot-link" style="left:352px;top:3469px"><b>»</b>Nemo enim ipsam</div>
<div class="abs foot-link" style="left:352px;top:3510px"><b>»</b>Voluptatem quia</div>
<div class="abs foot-link" style="left:352px;top:3550px"><b>»</b>Voluptas sit</div>
<div class="abs foot-link" style="left:352px;top:3591px"><b>»</b>Aspernatur</div>
<div class="abs foot-link" style="left:352px;top:3632px"><b>»</b>Aut odit aut fugit</div>

<div class="abs foot-head" style="left:620px">Contact Info</div>
<div class="abs" style="left:620px;top:3456px;font-size:17px;font-weight:700;color:var(--orange)">Brisk-Find</div>
<div class="abs foot-link" style="left:620px;top:3488px;line-height:22px">Harborline Avenue 14<br>Eastmere</div>
<svg class="abs" style="left:620px;top:3541px" width="14" height="14" viewBox="0 0 14 14"><path d="M3 1 L6 4 L4.5 6 Q6 9 8 9.5 L10 8 L13 11 L11 13 Q3 12 1 3 Z" fill="var(--orange)"/></svg>
<div class="abs foot-link" style="left:653px;top:3539px">1-800-555-0199</div>
<svg class="abs" style="left:620px;top:3572px" width="14" height="11" viewBox="0 0 14 11"><rect width="14" height="11" fill="var(--orange)"/><path d="M0 0 L7 6 L14 0" stroke="var(--footer)" stroke-width="1.5" fill="none"/></svg>
<div class="abs foot-link" style="left:653px;top:3569px">info@brisk-find.example</div>

<div class="abs foot-head" style="left:886px">Email Sign Up</div>
<div class="abs input">Email Address</div>
<div class="abs pill" style="left:884px;top:3526px;width:111px;height:45px;background:var(--orange);font-size:17px">Sign Up</div>
<div class="abs" style="left:1129px;top:3616px;width:54px;height:54px;border-radius:50%;background:var(--teal)"></div>

<div class="abs footer-bottom"></div>
<div class="abs" style="left:74px;top:3715px;font-size:12px;color:var(--footer-text)">Copyright © 2021 Company Name All Right Reserved</div>
<span class="abs social" style="left:936px" aria-label="Social link"></span>
<span class="abs social" style="left:978px" aria-label="Social link"></span>
<span class="abs social" style="left:1020px" aria-label="Social link"></span>
<span class="abs social" style="left:1060px" aria-label="Social link"></span>
<span class="abs social" style="left:1102px" aria-label="Social link"></span>
</footer>

</body>
</html>
```